Q&J RESTORATION

I want a brochure similiar to the example i've attached.
My company name is Q&J Restoration. The website is: Q-J-Restoration.example.
The phone number is 919.555.0147.

I don't like the "yellow" being the main color of the example so I'm open to suggestions. I want something CLEAN & Simple, like our logo . This will be a bi fold brochure

```html
<!DOCTYPE html>
<html lang="en">
<head>
<meta charset="UTF-8">
<title>Q&amp;J Restoration — Brochure Cover 2023</title>
<link href="https://fonts.googleapis.com/css2?family=Outfit:wght@400;500&display=swap" rel="stylesheet">
<style>
  :root {
    --brand-blue: #3478e3;
    --ink: #1b1b1b;
    --paper: #f4f4f4;
    --backdrop-white: #fdfdfd;
    --backdrop-light: #efefef;
    --backdrop-mid: #dcdcdc;
    --backdrop-dark: #c4c4c4;
    --photo-deep: #0a1a44;
    --photo-shade: #14307a;
    --photo-mid: #1e4fbf;
    --photo-bright: #3a78ea;
  }
  * { margin: 0; padding: 0; box-sizing: border-box; }
  html, body {
    width: 933px;
    height: 1200px;
    overflow: hidden;
    background: var(--paper);
    font-family: "Outfit", sans-serif;
    color: var(--ink);
  }
  .cover {
    position: relative;
    width: 933px;
    height: 1200px;
    overflow: hidden;
  }
  .cover__backdrop {
    position: absolute;
    inset: 0;
    background:
      radial-gradient(ellipse 70% 45% at 90% 15%, var(--backdrop-white) 0%, rgba(253,253,253,0) 70%),
      radial-gradient(ellipse 60% 40% at 10% 60%, rgba(196,196,196,0.55) 0%, rgba(196,196,196,0) 70%),
      linear-gradient(180deg, var(--backdrop-light) 0%, var(--backdrop-white) 30%, var(--backdrop-light) 60%, var(--backdrop-mid) 85%, var(--backdrop-dark) 100%);
  }
  .cover__top-band {
    position: absolute;
    top: 0; left: 0;
    width: 100%;
    height: 8px;
    background: var(--brand-blue);
  }

  .brand-name {
    position: absolute;
    left: 53px;
    top: 56px;
    width: 392px;
    height: 126px;
    display: flex;
    align-items: center;
    gap: 20px;
  }
  .brand-name__square {
    flex: none;
    width: 30px;
    height: 30px;
    background: var(--ink);
  }
  .brand-name__text {
    font-size: 50px;
    font-weight: 400;
    line-height: 1.05;
    letter-spacing: 1px;
    color: var(--ink);
  }
  .brand-name__line { display: block; }

  .edition-year {
    position: absolute;
    left: 746px;
    top: 46px;
    font-size: 38px;
    font-weight: 400;
    color: var(--ink);
  }
  .edition-tab {
    position: absolute;
    left: 846px;
    top: 53px;
    width: 87px;
    height: 32px;
    background: var(--brand-blue);
  }

  .halo-ring {
    position: absolute;
    left: 110px;
    top: 242px;
    width: 714px;
    height: 714px;
    border-radius: 50%;
    background: rgba(235, 235, 235, 0.55);
  }
  .feature-photo {
    position: absolute;
    left: 254px;
    top: 388px;
    width: 424px;
    height: 424px;
    border-radius: 50%;
    background:
      radial-gradient(ellipse 60% 45% at 45% 58%, rgba(58,120,234,0.9) 0%, rgba(58,120,234,0) 75%),
      linear-gradient(180deg, var(--photo-deep) 0%, var(--photo-shade) 28%, var(--photo-mid) 55%, var(--photo-shade) 85%, var(--photo-deep) 100%);
    box-shadow: 0 12px 40px rgba(0, 0, 0, 0.2);
  }

  .contact-bar {
    position: absolute;
    left: 53px;
    top: 1083px;
    width: 826px;
    height: 63px;
    border: 1px solid var(--brand-blue);
    display: flex;
    background: rgba(255, 255, 255, 0.45);
  }
  .contact-bar__item {
    display: flex;
    align-items: center;
    font-weight: 400;
    color: var(--ink);
  }
  .contact-bar__item--phone {
    width: 330px;
    padding-left: 52px;
    gap: 26px;
    font-size: 26px;
    border-right: 1px solid var(--brand-blue);
  }
  .contact-bar__item--web {
    flex: 1;
    padding-left: 70px;
    gap: 30px;
    font-size: 24px;
  }
  .contact-bar__icon { width: 30px; height: 30px; flex: none; }
</style>
</head>
<body>
  <main class="cover">
    <div class="cover__backdrop" role="img" aria-label="Faded black-and-white photo of a gutted basement under renovation with support posts, stairs and debris"></div>
    <div class="cover__top-band"></div>

    <div class="brand-name">
      <span class="brand-name__square"></span>
      <span class="brand-name__text">
        <span class="brand-name__line">Q&amp;J</span>
        <span class="brand-name__line">Restoration</span>
      </span>
    </div>

    <div class="edition-year">2023</div>
    <div class="edition-tab"></div>

    <div class="halo-ring"></div>
    <div class="feature-photo" role="img" aria-label="Blue-toned photo of a basement mid-restoration with exposed joists, steel props, a ladder and a wheelbarrow"></div>

    <div class="contact-bar">
      <div class="contact-bar__item contact-bar__item--phone">
        <svg class="contact-bar__icon" viewBox="0 0 24 24" aria-hidden="true">
          <path fill="#3478e3" d="M6.6 10.8a15.1 15.1 0 0 0 6.6 6.6l2.2-2.2a1 1 0 0 1 1-.25 11.4 11.4 0 0 0 3.6.57 1 1 0 0 1 1 1V20a1 1 0 0 1-1 1A17 17 0 0 1 3 4a1 1 0 0 1 1-1h3.5a1 1 0 0 1 1 1c0 1.25.2 2.45.57 3.570a1 1 0 0 1-.25 1z"/>
        </svg>
        <span>919 555 0147</span>
      </div>
      <div class="contact-bar__item contact-bar__item--web">
        <svg class="contact-bar__icon" viewBox="0 0 24 24" aria-hidden="true">
          <circle cx="12" cy="12" r="11" fill="#3478e3"/>
          <g fill="none" stroke="#fff" stroke-width="1.2">
            <ellipse cx="12" cy="12" rx="4.5" ry="11"/>
            <line x1="12" y1="1" x2="12" y2="23"/>
            <line x1="1" y1="12" x2="23" y2="12"/>
            <path d="M3 6.5h18M3 17.5h18"/>
          </g>
        </svg>
        <span>www.Q-J-Restoration.example</span>
      </div>
    </div>
  </main>
</body>
</html>
```